Business card design needed

I would like a one sided black business card with the information provided above. Refer to my website www.brightvolleyracquets.com.au for an example of colors I have used for my site, would like to keep this consistent for my business cards also, I will upload my logo below.

I am a new small business that provides tennis customers with racquet re stringing, tennis strings and accessories.

Industry/Entity Type

Small Business

Contact Information for Business Card

Bright Volley Tennis

Owen Whitby
Managing Director

brightvolleyracquets@mailbox.example
www.brightvolleyracquets.com.au
0491 726 305

Racquet Restringing/Tennis Strings/Accessories

Requirements
Must have
• Must have my logo and card must be black

```html
<!DOCTYPE html>
<html lang="en">
<head>
<meta charset="utf-8">
<title>Bright Volley Tennis – Business Card</title>
<link rel="stylesheet" href="https://fonts.googleapis.com/css2?family=PT+Sans:ital,wght@0,400;0,700;1,700&display=swap">
<style>
  :root {
    --backdrop: #e9e6e2;
    --card-black: #030404;
    --tennis-green: #b8d432;
    --deep-blue: #244f8c;
    --soft-blue: #6f8fd2;
    --text-white: #ffffff;
    --text-dark: #111111;
  }
  * { margin: 0; padding: 0; box-sizing: border-box; }
  html, body {
    width: 1200px;
    height: 750px;
    overflow: hidden;
    background: var(--backdrop);
    font-family: "PT Sans", Arial, sans-serif;
  }
  .card {
    position: absolute;
    left: 75px;
    top: 75px;
    width: 1050px;
    height: 600px;
    border-radius: 36px;
    overflow: hidden;
    background: var(--card-black);
  }
  .card-waves {
    position: absolute;
    inset: 0;
    width: 1050px;
    height: 600px;
  }
  .brand {
    position: absolute;
    left: 52px;
    top: 130px;
    display: flex;
    align-items: center;
    gap: 16px;
  }
  .brand-dot {
    width: 44px;
    height: 44px;
    border-radius: 50%;
    background: var(--tennis-green);
  }
  .brand-name {
    color: var(--tennis-green);
    font-weight: 700;
    font-size: 50px;
    line-height: 1;
    letter-spacing: 0.5px;
  }
  .services {
    position: absolute;
    left: 43px;
    top: 348px;
    list-style: none;
    color: var(--text-white);
    font-size: 26px;
    line-height: 35px;
  }
  .services li::before {
    content: "";
    display: inline-block;
    width: 9px;
    height: 9px;
    background: var(--text-white);
    margin-right: 8px;
    vertical-align: middle;
    position: relative;
    top: -3px;
  }
  .contact {
    position: absolute;
    right: 43px;
    top: 343px;
    text-align: right;
    color: var(--text-dark);
    font-size: 25px;
  }
  .contact-name {
    font-weight: 700;
    font-size: 33px;
    line-height: 40px;
  }
  .contact-title {
    line-height: 36px;
    margin-bottom: 10px;
  }
  .contact-line {
    line-height: 48px;
    white-space: nowrap;
  }
  .contact-label {
    font-weight: 700;
    font-style: italic;
    margin-right: 4px;
  }
</style>
</head>
<body>
  <div class="card">
    <svg class="card-waves" viewBox="0 0 1050 600" aria-hidden="true">
      <path fill="var(--deep-blue)"
            d="M0,470 C250,505 410,480 575,405 C740,325 875,225 1050,196 L1050,600 L0,600 Z"/>
      <path fill="var(--soft-blue)"
            d="M0,490 C250,530 420,500 585,420 C745,340 880,232 1050,203 L1050,600 L0,600 Z"/>
      <path fill="var(--card-black)"
            d="M0,538 C250,558 425,522 592,438 C752,353 884,240 1050,208 L1050,600 L0,600 Z"/>
      <path fill="var(--tennis-green)"
            d="M0,555 C250,575 430,540 600,455 C760,370 890,250 1050,215 L1050,600 L0,600 Z"/>
    </svg>

    <div class="brand">
      <span class="brand-dot"></span>
      <span class="brand-name">Bright Volley Tennis</span>
    </div>

    <ul class="services">
      <li>Racquet Restringing</li>
      <li>Tennis Strings</li>
      <li>Accessories</li>
    </ul>

    <div class="contact">
      <div class="contact-name">Owen Whitby</div>
      <div class="contact-title">Managing Director</div>
      <div class="contact-line"><span class="contact-label">p :</span>0491 726 305</div>
      <div class="contact-line"><span class="contact-label">e :</span>brightvolleyracquets@mailbox.example</div>
      <div class="contact-line"><span class="contact-label">w :</span>www.brightvolleyracquets.com.au</div>
    </div>
  </div>
</body>
</html>
```